Corporate Business Card

Very professional, Modern, Not to busy, include phone address email, website
(253) 617-4930, 18761 52nd Avenue S, Kent, WA 98047, martin@plumlinegroup.com, varkoworks.com

Target Market(s)

Manufacturing

Industry/Entity Type

Aero, machining, manufacturing, Off road racing

Contact Information for Business Card

Phone, address email, website

```html
<!DOCTYPE html>
<html lang="en">
<head>
<meta charset="utf-8">
<title>Varko Works — Business Card</title>
<link rel="stylesheet" href="https://fonts.googleapis.com/css2?family=Orbitron:wght@700&family=Roboto:wght@400;700&display=swap">
<style>
  :root {
    --backdrop: #2a2a2b;
    --navy: #2b3866;
    --navy-deep: #26325d;
    --red: #b82025;
    --white: #f2f2f2;
    --soft-white: #e4e6ee;
  }
  * { margin: 0; padding: 0; box-sizing: border-box; }
  html, body { width: 1200px; height: 1138px; overflow: hidden; }
  body {
    background: var(--backdrop);
    font-family: "Roboto", Arial, sans-serif;
    position: relative;
  }
  .card {
    position: absolute;
    border-radius: 16px;
    overflow: hidden;
    background: var(--navy);
  }
  .card--back { left: 274px; top: 186px; width: 623px; height: 376px; }
  .card--front { left: 276px; top: 608px; width: 618px; height: 374px; }

  .back-texture {
    position: absolute; inset: 0;
    background: linear-gradient(135deg, var(--navy-deep), var(--navy) 55%, #2f3d6e);
  }
  .brand {
    position: absolute;
    font-family: "Roboto", Arial, sans-serif;
    font-weight: 700;
    color: var(--white);
    letter-spacing: 1px;
    white-space: nowrap;
    text-transform: uppercase;
  }
  .card--back .brand { left: 54px; top: 282px; font-size: 34px; }
  .card--front .brand { left: 0; right: 0; top: 78px; text-align: center; font-size: 52px; letter-spacing: 2px; }

  .contact-band {
    position: absolute; left: 0; right: 0; top: 190px; height: 108px;
    background: var(--red);
  }
  .person-name {
    position: absolute; left: 60px; top: 50%; transform: translateY(-50%);
    font-family: "Orbitron", Arial, sans-serif; font-weight: 700;
    font-size: 24px; color: var(--white); letter-spacing: 0.5px;
  }
  .contact-list { position: absolute; left: 290px; top: 16px; list-style: none; }
  .contact-list li {
    display: flex; align-items: center; height: 25px;
    font-size: 17px; color: var(--soft-white);
  }
  .contact-list svg { width: 14px; height: 14px; margin-right: 15px; fill: var(--soft-white); }
  .address {
    position: absolute; left: 0; right: 0; top: 324px; text-align: center;
    font-size: 17px; color: var(--soft-white);
  }
</style>
</head>
<body>
  <section class="card card--back">
    <div class="back-texture" role="img" aria-label="Tone-on-tone embossed brand pattern on navy"></div>
    <div class="brand">Varko Works</div>
  </section>

  <section class="card card--front">
    <div class="brand">Varko Works</div>
    <div class="contact-band">
      <div class="person-name">DANIEL MARTIN</div>
      <ul class="contact-list">
        <li><svg viewBox="0 0 16 16" aria-hidden="true"><path d="M1 5c0-2 3-3 7-3s7 1 7 3v1h-3V5H4v1H1zM4 7h8l2 6H2z"/></svg>(253) 617-4930</li>
        <li><svg viewBox="0 0 16 16" aria-hidden="true"><path d="M1 3h14v10H1zM2.5 4.5L8 9l5.5-4.5v1L8 10 2.5 5.5z" fill-rule="evenodd"/></svg>martin@plumlinegroup.com</li>
        <li><svg viewBox="0 0 16 16" aria-hidden="true"><path d="M8 1a7 7 0 1 0 0 14A7 7 0 0 0 8 1zm0 1.3c.9 0 1.8 2 2 4.7H6c.2-2.7 1.1-4.7 2-4.7zM2.4 7h2.3c.1-1.8.4-3.3 1-4.3A5.7 5.7 0 0 0 2.4 7zm8.9 0h2.3a5.7 5.7 0 0 0-3.3-4.3c.6 1 .9 2.5 1 4.3zM2.4 9a5.7 5.7 0 0 0 3.3 4.3c-.6-1-.9-2.5-1-4.3zm3.6 0c.2 2.7 1.1 4.7 2 4.7s1.8-2 2-4.7zm5.3 0c-.1 1.8-.4 3.3-1 4.3A5.7 5.7 0 0 0 13.6 9z"/></svg>www.varkoworks.com</li>
      </ul>
    </div>
    <p class="address">18761 52nd Avenue S, Kent, WA 98047</p>
  </section>
</body>
</html>
```